Business Card Update, need to bring life to the card, two sided color

We need a new business card design, are moving and changing addresses and need a new look, we have the logos already attached but need a new style moving forward. Can incorporate the color of the logo (The Green) as well, maybe a solid back? We deal with safety products revolving around static electricity and safety lighting. Would like to keep same font in second logo as well.

Target Market(s)

Electrical Safety, Lighting

Contact Information for Business Card

Dale Fenwick
Vice President
Office: 770-555-4821
Cell: 770-555-3067
dale@tkfenwick.example
www.tkfenwick.example
4700 West Harbor Boulevard
Suite #150
Roswell, GA 30076

Font styles to use
Serif
Sans Serif

Requirements
Must have
• Since 1918
Nice to have
• Could use the 100 Year Logo for back of card, would like the back of card to be the same green as logo.
Should not have
• No black cards please.

```html
<!DOCTYPE html>
<html lang="en">
<head>
<meta charset="utf-8">
<title>T.K. Fenwick Business Card</title>
<link rel="stylesheet" href="https://fonts.googleapis.com/css2?family=Arimo:wght@700&family=Lato:wght@700&family=Open+Sans:wght@400;600&display=swap">
<style>
  :root {
    --brand-green: #079a5a;
    --card-white: #eeeeee;
    --ink: #1d1d1d;
    --rule: #a9a9a9;
    --backdrop: #8a8a8a;
  }
  * { margin: 0; padding: 0; box-sizing: border-box; }
  html, body { width: 1200px; height: 1200px; overflow: hidden; }
  body { background: var(--backdrop); position: relative; font-family: "Open Sans", sans-serif; }

  .card {
    position: absolute;
    top: 310px;
    width: 365px;
    height: 594px;
    box-shadow: 2px 3px 6px rgba(0,0,0,0.35);
    overflow: hidden;
  }
  .card--front { left: 234px; background: var(--card-white); text-align: center; }
  .card--back { left: 629px; background: var(--brand-green); width: 367px; }

  .brand-mark {
    position: absolute;
    top: 84px;
    left: 0; right: 0;
    display: flex;
    flex-direction: column;
    align-items: center;
    gap: 6px;
  }
  .brand-mark__dot {
    width: 70px; height: 70px;
    border-radius: 50%;
    background: var(--brand-green);
  }
  .brand-mark__name {
    font-family: "Arimo", sans-serif;
    font-weight: 700;
    font-size: 14px;
    color: var(--brand-green);
  }

  .company { position: absolute; left: 0; right: 0; top: 212px; color: var(--brand-green); font-family: "Arimo", sans-serif; font-weight: 700; }
  .company__name { font-size: 34px; line-height: 1; letter-spacing: 0.2px; }
  .company__sub { font-size: 16.5px; margin-top: 8px; letter-spacing: 0.6px; }
  .company__since { font-size: 13px; margin-top: 6px; letter-spacing: 1.5px; text-transform: uppercase; }

  .person { position: absolute; left: 0; right: 0; top: 338px; }
  .person__name { font-family: "Lato", sans-serif; font-weight: 700; font-size: 25px; color: var(--brand-green); line-height: 1.1; }
  .person__title { font-size: 16.5px; color: var(--ink); margin-top: -2px; }

  .rule { position: absolute; left: 106px; width: 180px; height: 1px; background: var(--rule); }
  .rule--upper { top: 397px; }
  .rule--lower { top: 507px; }

  .contact { position: absolute; left: 0; right: 0; top: 405px; font-size: 16.5px; line-height: 21.5px; color: var(--ink); }
  .contact__label { color: var(--brand-green); }
  .contact__web { color: var(--brand-green); font-weight: 600; letter-spacing: 0.3px; }

  .address { position: absolute; left: 0; right: 0; top: 514px; font-size: 16.5px; line-height: 21.5px; color: var(--ink); }

  .back-accent {
    position: absolute;
    left: 30px; top: 90px;
    width: 460px; height: 460px;
    border-radius: 50%;
    background: rgba(255,255,255,0.06);
  }
  .back-company { position: absolute; left: 0; right: 0; top: 490px; text-align: center; color: #fff; font-family: "Arimo", sans-serif; font-weight: 700; }
  .back-company__name { font-size: 35px; line-height: 1; }
  .back-company__sub { font-size: 17px; margin-top: 8px; letter-spacing: 0.6px; }
</style>
</head>
<body>
  <section class="card card--front" aria-label="Business card front">
    <div class="brand-mark">
      <div class="brand-mark__dot"></div>
      <span class="brand-mark__name">T.K. Fenwick</span>
    </div>
    <div class="company">
      <div class="company__name">T.K. Fenwick</div>
      <div class="company__sub">Manufacturing Company, Inc.</div>
      <div class="company__since">Since 1918</div>
    </div>
    <div class="person">
      <div class="person__name">Dale Fenwick</div>
      <div class="person__title">Vice President</div>
    </div>
    <div class="rule rule--upper"></div>
    <div class="contact">
      <div><span class="contact__label">P:</span> 770-555-4821</div>
      <div><span class="contact__label">M:</span> 770-555-3067</div>
      <div><span class="contact__label">E:</span> dale@tkfenwick.example</div>
      <div class="contact__web">www.tkfenwick.example</div>
    </div>
    <div class="rule rule--lower"></div>
    <div class="address">
      <div>4700 West Harbor Boulevard</div>
      <div>Suite #150, Roswell, GA 30076</div>
    </div>
  </section>

  <section class="card card--back" aria-label="Business card back">
    <div class="back-accent"></div>
    <div class="back-company">
      <div class="back-company__name">T.K. Fenwick</div>
      <div class="back-company__sub">Manufacturing Company, Inc.</div>
    </div>
  </section>
</body>
</html>
```